Namibia currently imports 60% of its food. Harvest Crest Oruva is an initiative which will assist Namibia to become self sustainable in terms of food production. We aim to do this through the development of 3 agricultural production zones which will include farming zones, local farmer assistance, processing and distribution of the final products. Please see our project overview attached.

```html
<!DOCTYPE html>
<html lang="en">
<head>
<meta charset="utf-8">
<title>Harvest Crest Oruva</title>
<link rel="stylesheet" href="https://fonts.googleapis.com/css2?family=Marcellus&family=Poppins:wght@400;500;600;700;800&display=swap">
<style>
:root{
  --green:#0b6b35;
  --green-dark:#085a2c;
  --tan:#c4a07f;
  --tan-dark:#b88f6b;
  --blue:#2aa7e0;
  --ink:#1d1d1d;
  --muted:#555;
  --footer:#141414;
  --white:#fff;
}
*{margin:0;padding:0;box-sizing:border-box}
html,body{width:1200px;height:5141px;overflow:hidden;background:#fff}
body{font-family:"Poppins",sans-serif;color:var(--ink);position:relative}
.serif{font-family:"Marcellus",serif;font-weight:400;letter-spacing:1px;text-transform:uppercase}
.abs{position:absolute}
.btn{position:absolute;display:flex;align-items:center;justify-content:center;background:var(--green);color:#fff;font-size:12px;border-radius:3px}
.ph{position:absolute}

/* header */
.site-header{position:absolute;top:0;left:0;width:1200px;height:88px;background:#fff}
.brand{position:absolute;left:142px;top:30px;font-family:"Marcellus",serif;font-size:26px;color:var(--green);letter-spacing:1px}
.nav{position:absolute;left:412px;top:34px;display:flex;gap:26px;font-size:12.5px;color:#222}
.nav .active{color:var(--green);font-weight:600}

/* hero */
.hero{position:absolute;top:88px;left:0;width:1200px;height:556px;overflow:hidden;
  background:linear-gradient(180deg,#b9c8d6 0%,#e8e3c0 32%,#f4ef9a 44%,#9bc43a 60%,#4f8f1f 80%,#2f6c15 100%)}
.hero h1{position:absolute;top:134px;width:100%;text-align:center;font-size:45px;line-height:52px;color:#111}
.hero p{position:absolute;top:248px;width:100%;text-align:center;font-size:14px;font-weight:500;color:#111}

/* titles */
.sec-title{position:absolute;width:1200px;text-align:center;font-size:36px;color:#111}
.sec-sub{position:absolute;width:1200px;text-align:center;font-size:12.5px;line-height:23px;color:#222}

.about-text{position:absolute;left:618px;top:882px;width:436px;font-size:12.5px;line-height:23px;color:#222}
.about-text p{margin-bottom:10px}

/* values band */
.values{position:absolute;top:1284px;left:0;width:1200px;height:338px;background:var(--tan)}
.value{position:absolute;top:58px;width:306px;height:222px;padding:32px 30px;color:#fff}
.value h3{font-size:17px;margin:14px 0 10px}
.value p{font-size:12px;line-height:22px;color:#fbf1e6}

/* projects */
.project{position:absolute;top:1798px;width:290px}
.project .img{height:186px}
.project h3{margin:22px 20px 0;font-size:17px;line-height:22px;color:#222}
.project p{margin:18px 18px 0;font-size:12px;line-height:22px;color:#333}
.readmore{position:absolute;font-size:11.5px;font-weight:600;color:var(--green);text-decoration:underline}
.arrow{position:absolute;font-size:20px;color:#111}

/* reviews */
.reviews{position:absolute;top:2324px;left:0;width:1200px;height:420px;background:var(--green);overflow:hidden}
.reviews h2{position:absolute;left:658px;top:96px;font-size:32px;color:#fff}
.reviews blockquote{position:absolute;left:658px;top:146px;width:410px;font-size:12px;line-height:23px;color:#e9f3ec}

/* zones */
.legend{position:absolute;left:142px;display:flex;align-items:center;gap:12px;font-size:14px;font-weight:500}
.legend i{width:18px;height:18px;display:block}

/* stats */
.stat{position:absolute;top:3294px;width:398px;height:334px;color:#fff;text-align:center}
.stat .num{position:absolute;top:92px;width:100%;font-size:88px;font-weight:800;letter-spacing:2px;color:rgba(255,255,255,.85)}
.stat .lbl{position:absolute;top:208px;width:100%;font-size:19px;font-weight:600}

/* news */
.news{position:absolute;top:3800px;width:290px;height:440px;border:1px solid #ddd;background:#fff}
.news .img{height:212px}
.news .date{margin:28px 28px 0;font-size:12px;color:#444}
.news h4{margin:16px 28px 0;font-size:13px;font-weight:600;line-height:24px}
.news p{margin:12px 28px 0;font-size:12px;line-height:24px;color:#444}
.circ{position:absolute;width:38px;height:38px;border-radius:50%;border:1px solid #ccc;background:#fff;display:flex;align-items:center;justify-content:center;font-size:16px}

/* newsletter */
.newsletter{position:absolute;left:142px;top:4396px;width:918px;height:316px;background:var(--green);overflow:hidden}
.newsletter h2{position:absolute;left:70px;top:92px;font-size:34px;color:#fff}
.newsletter p{position:absolute;left:70px;top:144px;width:420px;font-size:12px;line-height:23px;color:#e8f2eb}

/* footer */
.footer{position:absolute;top:4800px;left:0;width:1200px;height:306px;background:var(--footer);color:#fff}
.footer h5{position:absolute;top:58px;font-size:18px}
.links{position:absolute;left:542px;top:92px;font-size:12px;line-height:29px}
.contact{position:absolute;left:826px;font-size:12px;line-height:20px;display:flex;gap:14px}
.contact .ic{width:28px;height:28px;background:var(--tan);display:flex;align-items:center;justify-content:center;flex:none}
.bottom{position:absolute;top:5106px;left:0;width:1200px;height:35px;background:var(--green);color:#fff;font-size:12px}
</style>
</head>
<body>

<header class="site-header">
  <div class="brand">HARVEST CREST ORUVA</div>
  <nav class="nav">
    <span class="active">Home</span><span>About Us</span><span>Our Projects</span><span>Farmer Resources</span><span>News &amp; Updates</span>
  </nav>
  <div class="btn" style="left:932px;top:22px;width:128px;height:42px">Contact Us</div>
</header>

<section class="hero" role="img" aria-label="Sunlit field of young green crops under a bright sky">
  <h1 class="serif">Empowering Namibia to<br>achieve food independence</h1>
  <p>Reducing imports by fostering local agricultural production</p>
  <div class="btn" style="left:498px;top:296px;width:204px;height:42px">Learn About Our Projects</div>
  <svg class="abs" style="left:0;bottom:0" width="1200" height="120" viewBox="0 0 1200 120">
    <path d="M0 90 C250 20 420 40 620 60 C820 80 1000 40 1200 20 L1200 120 L0 120Z" fill="#fff"/>
    <path d="M0 90 C250 20 420 40 620 60 C820 80 1000 40 1200 20 L1200 34 C1000 56 820 96 620 78 C420 60 250 36 0 104Z" fill="var(--green)"/>
  </svg>
</section>

<h2 class="sec-title serif" style="top:724px">About Us</h2>
<p class="sec-sub" style="top:774px;left:150px;width:900px">Lorem ipsum dolor sit amet, consectetur adipiscing elit, sed do eiusmod tempor incididunt ut labore et dolore magna aliqua. Ut enim ad minim veniam, quis nostrud exercitation ullamco laboris nisi ut aliquip ex ea commodo consequat.</p>
<div class="ph" style="left:142px;top:846px;width:412px;height:352px;background:linear-gradient(180deg,#6f9a3c 0%,#4d6e2c 45%,#7a5a3a 60%,#c7a070 80%,#5b4128 100%)" role="img" aria-label="Freshly harvested potatoes on soil beside crop rows"></div>
<div class="about-text">
  <p>Lorem Ipsum is simply dummy text of the printing and typesetting industry. Lorem Ipsum has been the industry's standard dummy text ever since the 1500s, when an unknown printer took a galley of type and scrambled it to make a type specimen book.</p>
  <p>It is a long established fact that a reader will be distracted by the readable content of a page when looking at its layout.</p>
  <p>Lorem ipsum dolor sit amet, consectetur adipiscing elit, sed do eiusmod tempor incididunt ut labore et dolore magna aliqua.</p>
</div>
<div class="btn" style="left:618px;top:1112px;width:126px;height:40px">Read More</div>

<section class="values">
  <div class="value" style="left:142px;border-right:1px solid rgba(255,255,255,.35)">
    <svg width="40" height="40" viewBox="0 0 40 40" fill="none" stroke="#fff" stroke-width="2"><circle cx="20" cy="20" r="16"/><circle cx="20" cy="20" r="9"/><circle cx="20" cy="20" r="2"/><path d="M20 20 L34 6 M30 6h4v4"/></svg>
    <h3 class="serif">Our Mission</h3>
    <p>Lorem ipsum dolor sit amet, dolor ex consectetur adipiscing elit, sed do ut eiusmod tempor.</p>
  </div>
  <div class="value" style="left:448px;border-right:1px solid rgba(255,255,255,.35)">
    <svg width="40" height="40" viewBox="0 0 40 40" fill="none" stroke="#fff" stroke-width="2"><circle cx="20" cy="11" r="6"/><path d="M8 36 C8 24 32 24 32 36Z"/><circle cx="8" cy="20" r="4"/><circle cx="32" cy="20" r="4"/></svg>
    <h3 class="serif">Our Vision</h3>
    <p>Lorem ipsum dolor sit amet, dolor ex consectetur adipiscing elit, sed do ut eiusmod tempor.</p>
  </div>
  <div class="value" style="left:754px">
    <svg width="40" height="40" viewBox="0 0 40 40" fill="none" stroke="#fff" stroke-width="2"><circle cx="20" cy="22" r="8"/><circle cx="20" cy="22" r="3"/><path d="M20 10v-4M20 38v-4M8 22H4M36 22h-4M11 13l-3-3M29 13l3-3M11 31l-3 3M29 31l3 3"/></svg>
    <h3 class="serif">Our Values</h3>
    <p>Lorem ipsum dolor sit amet, dolor ex consectetur adipiscing elit, sed do ut eiusmod tempor.</p>
  </div>
</section>

<h2 class="sec-title serif" style="top:1698px">Our Projects</h2>
<p class="sec-sub" style="top:1750px">Ut enim ad minim veniam, quis nostrud exercitation ullamco laboris nisi ut aliquip ex ea commodo consequat.</p>
<div class="arrow" style="left:88px;top:1968px">&#8249;</div>
<div class="arrow" style="left:1100px;top:1968px">&#8250;</div>
<article class="project" style="left:142px">
  <div class="img" style="background:linear-gradient(180deg,#9cc0e0 0%,#d7e4ee 30%,#7aa64a 45%,#4f8a2b 100%)" role="img" aria-label="Green crop field with solar panels in the distance"></div>
  <h3 class="serif">Agricultural<br>Production Zones</h3>
  <p>Lorem Ipsum is simply dummy text of the printing and typesetting industry.</p>
</article>
<article class="project" style="left:456px">
  <div class="img" style="background:linear-gradient(90deg,#2f6a1c,#6aa33a 50%,#3c7a22)" role="img" aria-label="Farmer checking a tablet among tall maize plants"></div>
  <h3 class="serif">Local Farmer<br>Assistance</h3>
  <p>Lorem Ipsum is simply dummy text of the printing and typesetting industry.</p>
</article>
<article class="project" style="left:770px">
  <div class="img" style="background:linear-gradient(180deg,#a9c6e2 0%,#6f9b4e 40%,#8a5a3a 75%,#c2533a 100%)" role="img" aria-label="Workers loading crates of harvested produce beside a tractor"></div>
  <h3 class="serif">Processing and<br>Distribution</h3>
  <p>Lorem Ipsum is simply dummy text of the printing and typesetting industry.</p>
</article>
<span class="readmore" style="left:160px;top:2128px">Read More</span>
<span class="readmore" style="left:474px;top:2128px">Read More</span>
<span class="readmore" style="left:788px;top:2128px">Read More</span>
<div class="btn" style="left:536px;top:2198px;width:128px;height:40px">Contact Us</div>

<section class="reviews">
  <div class="ph" style="left:0;top:0;width:600px;height:420px;background:linear-gradient(135deg,#5d7a38 0%,#8a6a3c 45%,#a8774c 70%,#6a8a3a 100%)" role="img" aria-label="Farmers hoeing soil in a field"></div>
  <svg class="abs" style="left:900px;top:180px" width="260" height="240" viewBox="0 0 260 240" fill="none" stroke="rgba(255,255,255,.08)" stroke-width="18"><path d="M20 20 C140 40 200 120 220 240"/></svg>
  <h2 class="serif">Customer Reviews</h2>
  <blockquote>"Sed ut perspiciatis unde omnis iste natus error sit voluptatem accusantium doloremque laudantium, totam rem aperiam, ex eaque ipsa quae ab illo inventore veritatis et quasi architecto beatae vitae dicta sunt explicabo. Nemo enim ipsam."</blockquote>
  <div class="ph" style="left:658px;top:266px;width:50px;height:50px;border-radius:50%;background:#c49a6c;border:2px solid #fff" role="img" aria-label="Reviewer portrait"></div>
  <div class="abs" style="left:720px;top:270px;font-size:14px;font-weight:600;color:#fff">Daniel Mareka</div>
  <svg class="abs" style="left:720px;top:294px" width="92" height="16" viewBox="0 0 92 16">
    <g fill="#f7b500">
      <polygon points="8,0 10,6 16,6 11,10 13,16 8,12 3,16 5,10 0,6 6,6"/>
      <polygon transform="translate(19 0)" points="8,0 10,6 16,6 11,10 13,16 8,12 3,16 5,10 0,6 6,6"/>
      <polygon transform="translate(38 0)" points="8,0 10,6 16,6 11,10 13,16 8,12 3,16 5,10 0,6 6,6"/>
      <polygon transform="translate(57 0)" points="8,0 10,6 16,6 11,10 13,16 8,12 3,16 5,10 0,6 6,6"/>
      <polygon transform="translate(76 0)" points="8,0 10,6 16,6 11,10 13,16 8,12 3,16 5,10 0,6 6,6"/>
    </g>
  </svg>
</section>

<h2 class="serif abs" style="left:142px;top:2846px;font-size:35px;line-height:38px;color:#111">Agricultural<br>Production Zones</h2>
<p class="abs" style="left:142px;top:2926px;width:440px;font-size:12px;line-height:23px">Ut enim ad minim veniam, quis nostrud exercitation ullamco laboris nisi ut aliquip ex ea commodo consequat.</p>
<div class="legend" style="top:3000px"><i style="background:var(--green)"></i>Farming Zones</div>
<div class="legend" style="top:3046px"><i style="background:var(--tan)"></i>Local Farmer Assistance</div>
<div class="legend" style="top:3092px"><i style="background:var(--blue)"></i>Processing and Distribution</div>
<div class="btn" style="left:142px;top:3142px;width:126px;height:42px">Contact Us</div>
<div class="ph" style="left:624px;top:2830px;width:366px;height:376px;background:linear-gradient(135deg,#1f7a3c 0%,#2aa7e0 40%,#c4a07f 60%,#1f7a3c 100%);opacity:.9" role="img" aria-label="Map of Namibia divided into farming, farmer assistance and processing regions"></div>
<div class="abs" style="left:846px;top:3010px;font-family:'Marcellus',serif;font-size:24px;color:var(--green)">HARVEST CREST ORUVA</div>

<div class="stat" style="left:0;background:linear-gradient(180deg,#1a3d8a 0%,#4a78b8 45%,#3f7a2a 70%,#2a5a18 100%)" role="img" aria-label="Cultivated farmland under a blue sky">
  <div class="num">75%</div><div class="lbl">Hectares of Land Cultivated</div>
</div>
<div class="stat" style="left:402px;background:linear-gradient(135deg,#3f7a4a,#5c8f5a 50%,#2f6a3a)" role="img" aria-label="Farmer working with crops">
  <div class="num">25%</div><div class="lbl">Farmers Assisted</div>
</div>
<div class="stat" style="left:804px;background:linear-gradient(180deg,#5c6670 0%,#7d8a8e 45%,#3e6a2a 75%,#24501a 100%)" role="img" aria-label="Grain silos beside a maize field">
  <div class="num">85%</div><div class="lbl">Reduction In Food Imports</div>
</div>

<h2 class="sec-title serif" style="top:3702px">Latest News &amp; Updates</h2>
<p class="sec-sub" style="top:3756px">Lorem ipsum dolor sit amet, consectetur adipiscing elit, sed do eiusmod tempor incididunt ut labore et dolore magna aliqua.</p>
<div class="circ" style="left:78px;top:4006px">&#8249;</div>
<div class="circ" style="left:1084px;top:4006px">&#8250;</div>
<article class="news" style="left:142px">
  <div class="img" style="background:linear-gradient(180deg,#5f8f3a,#3f6a22 50%,#8a5a3a)" role="img" aria-label="Farmer tending crops in a field"></div>
  <div class="date">10, June 2024</div>
  <h4>Lorem Ipsum Dolor Sit Ametco Adipiscing Eliter Sed Diam</h4>
  <p>Lorem ipsum dolor sit ametewroe ctetuer adipiscing eliter sed diam utlaoreeteere sed diam</p>
</article>
<article class="news" style="left:456px">
  <div class="img" style="background:linear-gradient(180deg,#9cc0e0 0%,#d7e4ee 30%,#7aa64a 45%,#4f8a2b 100%)" role="img" aria-label="Crop field with solar panels"></div>
  <div class="date">28, May 2024</div>
  <h4>Lorem Ipsum Dolor Sit Ametco Adipiscing Eliter Sed Diam</h4>
  <p>Lorem ipsum dolor sit ametewroe ctetuer adipiscing eliter sed diam utlaoreeteere sed diam</p>
</article>
<article class="news" style="left:770px">
  <div class="img" style="background:linear-gradient(90deg,#4f7a2a,#e0a23a 40%,#5f8a30)" role="img" aria-label="Farmers holding a basket of harvest"></div>
  <div class="date">14, April 2024</div>
  <h4>Lorem Ipsum Dolor Sit Ametco Adipiscing Eliter Sed Diam</h4>
  <p>Lorem ipsum dolor sit ametewroe ctetuer adipiscing eliter sed diam utlaoreeteere sed diam</p>
</article>
<span class="readmore" style="left:170px;top:4202px">Read More</span>
<span class="readmore" style="left:484px;top:4202px">Read More</span>
<span class="readmore" style="left:798px;top:4202px">Read More</span>
<div class="btn" style="left:490px;top:4276px;width:220px;height:42px">View All News And Updates</div>

<section class="newsletter">
  <div class="ph" style="left:520px;top:40px;width:398px;height:276px;background:radial-gradient(ellipse at 50% 50%,rgba(196,160,127,.45),rgba(11,107,53,0) 70%)" role="img" aria-label="Faded image of a smiling farmer"></div>
  <h2 class="serif">Newsletter Sign Up</h2>
  <p>Sed ut perspiciatis unde omnis iste natus error sit voluptatem accusantium doloremque laudantium, totam rem aperiam.</p>
  <div class="abs" style="left:72px;top:216px;width:308px;height:40px;background:#fff;font-size:12px;padding:12px 22px;color:#222">Enter Your Email Address</div>
  <div class="abs" style="left:386px;top:216px;width:128px;height:40px;background:var(--tan);color:#fff;font-size:12px;display:flex;align-items:center;justify-content:center">Subscribe</div>
</section>

<footer class="footer">
  <div class="abs" style="left:142px;top:120px;font-family:'Marcellus',serif;font-size:30px;color:var(--green)">HARVEST CREST<br>ORUVA</div>
  <h5 class="serif" style="left:542px">Quick Links</h5>
  <div class="links">• Home<br>• About Us<br>• Our Projects<br>• Farmer Resources<br>• News &amp; Updates<br>• Contact Us</div>
  <h5 class="serif" style="left:826px">Contact Details</h5>
  <div class="contact" style="top:96px"><span class="ic"><svg width="14" height="14" viewBox="0 0 14 14"><path d="M7 1a4 4 0 0 1 4 4c0 3-4 8-4 8S3 8 3 5a4 4 0 0 1 4-4z" fill="#fff"/></svg></span><span>123, Building Name, Street City,<br>State XY 123456</span></div>
  <div class="contact" style="top:156px"><span class="ic"><svg width="14" height="12" viewBox="0 0 14 12"><rect x="1" y="1" width="12" height="10" fill="none" stroke="#fff" stroke-width="1.5"/><path d="M1 1l6 5 6-5" fill="none" stroke="#fff" stroke-width="1.5"/></svg></span><span>Email<br>info@harvestcrestoruva.com</span></div>
  <div class="contact" style="top:214px"><span class="ic"><svg width="14" height="14" viewBox="0 0 14 14"><path d="M3 1l3 3-2 2c1 2 2 3 4 4l2-2 3 3-2 2C6 13 1 8 1 3z" fill="#fff"/></svg></span><span>Phone<br>123-456-7890</span></div>
</footer>
<div class="bottom">
  <span class="abs" style="left:142px;top:9px">©2024 Harvest Crest Oruva. All Rights Reserved.</span>
  <span class="abs" style="left:972px;top:11px;display:flex;gap:10px">
    <i style="width:13px;height:13px;border-radius:50%;background:#fff;display:block"></i>
    <i style="width:13px;height:13px;border-radius:50%;background:#fff;display:block"></i>
    <i style="width:13px;height:13px;border-radius:50%;background:#fff;display:block"></i>
    <i style="width:13px;height:13px;border-radius:50%;background:#fff;display:block"></i>
  </span>
</div>

</body>
</html>
```